Income Tax Flyer - Updates Needed

Just need to update this flyer design and give it a new look. We would like to keep all the same wording but make it stand out a little more. Our selling point is the "Same Day Tax Advance up to $6,000"

Lending, Small Loans, Tax Services, Title Loans, Personal Loans

```html
<!DOCTYPE html>
<html lang="en">
<head>
<meta charset="UTF-8">
<title>Keystone Financial Group – Same Day Tax Advance Flyer</title>
<link href="https://fonts.googleapis.com/css2?family=Poppins:wght@300;400;600;700;800&display=swap" rel="stylesheet">
<style>
  :root {
    --forest: #0a4f2b;
    --forest-deep: #073a20;
    --sage: #88a897;
    --sage-tint: #eef3f0;
    --signal-red: #c02026;
    --paper: #ffffff;
    --photo-light: #e9eef1;
    --photo-mid: #b9c6cf;
    --photo-warm: #d9b08a;
  }
  * { margin: 0; padding: 0; box-sizing: border-box; }
  html, body { width: 800px; height: 1200px; overflow: hidden; background: var(--paper); }
  .flyer {
    position: relative;
    width: 800px;
    height: 1200px;
    overflow: hidden;
    background: var(--sage-tint);
    font-family: "Poppins", sans-serif;
    color: var(--forest);
  }

  /* Header */
  .masthead {
    position: absolute;
    left: 0; top: 0;
    width: 800px; height: 110px;
    background: var(--paper);
  }
  .brand {
    position: absolute;
    left: 48px; top: 28px;
    display: flex;
    align-items: center;
    gap: 14px;
  }
  .brand-mark {
    width: 40px; height: 40px;
    background: var(--signal-red);
  }
  .brand-name {
    font-size: 34px; font-weight: 700; line-height: 36px; letter-spacing: -0.5px;
  }
  .brand-tag {
    font-size: 12px; font-weight: 600; letter-spacing: 4px; line-height: 16px;
  }
  .tax-season {
    position: absolute;
    right: 48px; top: 42px;
    font-size: 15px; font-weight: 600; letter-spacing: 3px;
    color: var(--sage);
  }

  /* Hero */
  .hero {
    position: absolute;
    left: 0; top: 110px;
    width: 800px; height: 520px;
    background: var(--forest);
    overflow: hidden;
    color: var(--paper);
  }
  .hero-rings { position: absolute; inset: 0; }
  .offer-tag {
    position: absolute;
    left: 48px; top: 40px;
    padding: 8px 20px;
    background: var(--signal-red);
    font-size: 22px; font-weight: 700; letter-spacing: 2px; line-height: 30px;
  }
  .offer-lead {
    position: absolute;
    left: 50px; top: 102px;
    font-size: 34px; font-weight: 300; line-height: 40px;
  }
  .offer-amount {
    position: absolute;
    left: 42px; top: 128px;
    font-size: 150px; font-weight: 800; line-height: 170px; letter-spacing: -4px;
  }
  .headline {
    position: absolute;
    left: 48px; top: 318px;
    font-size: 34px; font-weight: 700; line-height: 42px;
  }
  .headline .range { color: var(--sage); }
  .subline {
    position: absolute;
    left: 48px; top: 420px;
    font-size: 24px; font-weight: 300; line-height: 32px;
  }
  .subline strong { font-weight: 700; }

  /* Middle */
  .perks {
    position: absolute;
    left: 48px; top: 680px;
    width: 320px;
    list-style: none;
  }
  .perks li {
    display: flex;
    align-items: flex-start;
    gap: 16px;
    padding-bottom: 24px;
    margin-bottom: 24px;
    border-bottom: 2px solid var(--sage);
    font-size: 26px; font-weight: 800; line-height: 32px;
  }
  .perks li:last-child { border-bottom: none; }
  .perks svg { flex: none; margin-top: 1px; }
  .portrait {
    position: absolute;
    left: 400px; top: 665px;
    width: 352px; height: 370px;
    border-radius: 24px;
    background:
      radial-gradient(circle at 52% 40%, var(--photo-warm) 0%, rgba(217,176,138,0) 32%),
      linear-gradient(120deg, var(--photo-mid) 0%, var(--photo-light) 45%, #f6f8f9 70%, var(--photo-mid) 100%);
    box-shadow: 14px 14px 0 var(--sage);
  }

  /* Contact */
  .contact-bar {
    position: absolute;
    left: 0; top: 1075px;
    width: 800px; height: 125px;
    background: var(--signal-red);
    display: flex;
    align-items: center;
    justify-content: center;
    gap: 18px;
    color: var(--paper);
  }
  .contact-text { font-size: 30px; font-weight: 800; line-height: 36px; }
</style>
</head>
<body>
<main class="flyer">
  <header class="masthead">
    <div class="brand">
      <span class="brand-mark" aria-hidden="true"></span>
      <div>
        <div class="brand-name">Keystone</div>
        <div class="brand-tag">FINANCIAL GROUP</div>
      </div>
    </div>
    <div class="tax-season">TAX SEASON</div>
  </header>

  <section class="hero">
    <svg class="hero-rings" width="800" height="520" viewBox="0 0 800 520" aria-hidden="true">
      <circle cx="760" cy="120" r="230" fill="var(--forest-deep)"/>
      <circle cx="760" cy="120" r="300" fill="none" stroke="var(--sage)" stroke-opacity="0.35" stroke-width="2"/>
    </svg>
    <div class="offer-tag">SAME DAY TAX ADVANCE</div>
    <div class="offer-lead">up to</div>
    <div class="offer-amount">$6,000</div>
    <h1 class="headline">Apply here for<br><span class="range">$5000-6000</span> today!</h1>
    <p class="subline">File your taxes and apply for an<br><strong>Ample Advance</strong>.</p>
  </section>

  <ul class="perks">
    <li>
      <svg width="32" height="32" viewBox="0 0 32 32" aria-hidden="true"><circle cx="16" cy="16" r="16" fill="var(--signal-red)"/><path d="M9 16.5l4.5 4.5L23 11.5" fill="none" stroke="#fff" stroke-width="3" stroke-linecap="round" stroke-linejoin="round"/></svg>
      <span>Available in 24<br>hours or less</span>
    </li>
    <li>
      <svg width="32" height="32" viewBox="0 0 32 32" aria-hidden="true"><circle cx="16" cy="16" r="16" fill="var(--signal-red)"/><path d="M9 16.5l4.5 4.5L23 11.5" fill="none" stroke="#fff" stroke-width="3" stroke-linecap="round" stroke-linejoin="round"/></svg>
      <span>Choose your<br>amount</span>
    </li>
    <li>
      <svg width="32" height="32" viewBox="0 0 32 32" aria-hidden="true"><circle cx="16" cy="16" r="16" fill="var(--signal-red)"/><path d="M9 16.5l4.5 4.5L23 11.5" fill="none" stroke="#fff" stroke-width="3" stroke-linecap="round" stroke-linejoin="round"/></svg>
      <span>Quick and easy</span>
    </li>
  </ul>

  <div class="portrait" role="img" aria-label="Photo of a smiling professional woman in glasses holding a tablet in a bright office"></div>

  <footer class="contact-bar">
    <svg width="34" height="34" viewBox="0 0 24 24" aria-hidden="true"><path d="M6.6 10.8a15.1 15.1 0 006.6 6.6l2.2-2.2a1 1 0 011-.25 11.4 11.4 0 003.6.57 1 1 0 011 1V20a1 1 0 01-1 1A17 17 0 013 4a1 1 0 011-1h3.5a1 1 0 011 1c0 1.25.2 2.45.57 3.57a1 1 0 01-.25 1z" fill="#fff"/></svg>
    <p class="contact-text">Contact Details here</p>
  </footer>
</main>
</body>
</html>
```